first fantastic look and impression

We are looking for a concept for letterhead, business card, emailfooter and template for invoices or offers for our company in the consultation business.
The dancer is a symbol who we are: it looks simple, but there is a lot of hard work and many years of training in this movement. The look is also what we want: elegant, modern, strong, with a touch of extravaganza
Target Market(s)
Hotelbusiness , Consulting
Font styles to use
Sans Serif
Other font styles liked:
- please give us a option we are open
Requirements
Must have
- We are not typical consultants but sparring partners and coaches for the hotel and that should also be expressed in the design. Maybe there is an icon that supports the whole thing. We are more modern and bolder than our industry colleagues.
we are modern, fresh, agile, fast
Nice to have
- a icon

```html
<!DOCTYPE html>
<html lang="en">
<head>
<meta charset="UTF-8">
<title>Halden+Partner – Business Card</title>
<link href="https://fonts.googleapis.com/css2?family=Montserrat:wght@500;700&family=Roboto:wght@400&display=swap" rel="stylesheet">
<style>
  :root {
    --backdrop: #9a9a9a;
    --card-white: #f7f7f6;
    --card-black: #151517;
    --ink-navy: #1f2233;
    --ink-grey: #6a6b70;
    --silver: #b9babd;
    --gilded-edge: #a88a3c;
  }
  * { margin: 0; padding: 0; box-sizing: border-box; }
  html, body {
    width: 1200px; height: 963px; overflow: hidden;
    background: var(--backdrop);
  }
  .stage {
    position: relative; width: 1200px; height: 963px;
    display: flex; flex-direction: column; align-items: center; justify-content: center; gap: 56px;
  }
  .card {
    position: relative; width: 600px; height: 343px;
    border-bottom: 3px solid var(--gilded-edge);
    box-shadow: 0 18px 40px rgba(0,0,0,0.22);
  }
  .card--front { background: var(--card-white); }
  .card--back { background: var(--card-black); display: flex; align-items: center; justify-content: center; }

  .contact-block { position: absolute; left: 60px; top: 112px; }
  .contact-name {
    font-family: 'Montserrat', sans-serif; font-weight: 700; font-size: 19px;
    color: var(--ink-navy); letter-spacing: 0.2px;
  }
  .contact-role {
    font-family: 'Montserrat', sans-serif; font-weight: 500; font-size: 15px;
    color: var(--ink-grey); margin-bottom: 14px;
  }
  .contact-list { list-style: none; }
  .contact-item {
    display: flex; align-items: center; gap: 10px;
    font-family: 'Roboto', sans-serif; font-size: 16px; color: var(--ink-grey);
    line-height: 1.55;
  }
  .contact-icon { width: 16px; height: 16px; flex: none; fill: var(--ink-navy); }
  .contact-icon--line { fill: none; stroke: var(--ink-navy); stroke-width: 1.6; }

  .wordmark {
    font-family: 'Montserrat', sans-serif; font-weight: 500;
    color: var(--ink-navy); letter-spacing: 3px; text-transform: uppercase;
  }
  .card--front .wordmark { position: absolute; right: 56px; top: 130px; font-size: 17px; }
  .card--back .wordmark { color: var(--silver); font-size: 30px; letter-spacing: 6px; }
</style>
</head>
<body>
<main class="stage">
  <section class="card card--front">
    <div class="contact-block">
      <p class="contact-name">MARA LINDQVIST</p>
      <p class="contact-role">Managing Director</p>
      <ul class="contact-list">
        <li class="contact-item">
          <svg class="contact-icon" viewBox="0 0 24 24"><path d="M6.6 10.8a15.1 15.1 0 0 0 6.6 6.6l2.2-2.2c.3-.3.7-.4 1-.2 1.1.4 2.3.6 3.6.6.6 0 1 .4 1 1V20c0 .6-.4 1-1 1A17 17 0 0 1 3 4c0-.6.4-1 1-1h3.5c.6 0 1 .4 1 1 0 1.3.2 2.5.6 3.6.1.3 0 .7-.2 1z"/></svg>
          +43512480339
        </li>
        <li class="contact-item">
          <svg class="contact-icon" viewBox="0 0 24 24"><path d="M2 5h20v14H2z M3.5 6.5 12 13l8.5-6.5" fill="var(--ink-navy)" stroke="var(--card-white)" stroke-width="1.4"/></svg>
          info@haldenpartner.com
        </li>
        <li class="contact-item">
          <svg class="contact-icon contact-icon--line" viewBox="0 0 24 24"><circle cx="12" cy="12" r="9"/><path d="M3 12h18M12 3c3 3 3 15 0 18M12 3c-3 3-3 15 0 18"/></svg>
          www.haldenpartner.com
        </li>
        <li class="contact-item">
          <svg class="contact-icon" viewBox="0 0 24 24"><path d="M12 2a7 7 0 0 0-7 7c0 5 7 13 7 13s7-8 7-13a7 7 0 0 0-7-7zm0 9.5A2.5 2.5 0 1 1 12 6.5a2.5 2.5 0 0 1 0 5z"/></svg>
          Innsbruck/Austria
        </li>
      </ul>
    </div>
    <p class="wordmark">Halden+Partner</p>
  </section>

  <section class="card card--back">
    <p class="wordmark">Halden+Partner</p>
  </section>
</main>
</body>
</html>
```